Create banner ads for a digital product that deletes personal information from the web

The context of the banners is general advertisement for our service.
Please provide us with a set of static and flash/gif banners in the following standard sizes for the theme you create:
160x600
300x250
300x600
320x250
336x280
728x90
Please see our website for logo (just our name) and theme ideas - please follow similar color/font schemes if possible. www.quillbranchdata.com
Our company is an online service that deletes personal information from the internet for our members (automated opt-outs and content removal). Our target audience is anyone who wishes to protect their personal information from being on the internet (i.e. prefer to fly under the internet radar, for example). This is a product for U.S. residents who value privacy and online reputation. We seek to provide members with control of what 300+ websites are sharing about them – removing names, addresses, ages, phone numbers, email addresses, children’s information, home/property value information etc.
Internet

```html
<!DOCTYPE html>
<html lang="en">
<head>
<meta charset="utf-8">
<title>QuillBranch – Personal Privacy Banner</title>
<link href="https://fonts.googleapis.com/css2?family=Lato:wght@400;700;900&display=swap" rel="stylesheet">
<style>
  :root {
    --ink: #111111;
    --white: #ffffff;
    --sky-glow: #fffbe8;
    --sky-gold: #f3c35a;
    --sky-amber: #d98a2b;
    --sky-brown: #7a4a22;
    --sky-blue: #8aa3b6;
    --btn-top: #7ccf55;
    --btn-bottom: #3f9d2c;
    --btn-edge: #2f7f20;
  }
  * { margin: 0; padding: 0; box-sizing: border-box; }
  html, body { width: 1200px; height: 148px; overflow: hidden; background: var(--white); }
  .banner {
    position: relative;
    width: 1200px;
    height: 148px;
    overflow: hidden;
    font-family: "Lato", Arial, sans-serif;
  }
  .sky-photo {
    position: absolute;
    inset: 0;
    background:
      radial-gradient(ellipse 420px 120px at 520px 55px, var(--sky-glow) 0%, rgba(255,248,220,0.85) 35%, rgba(243,195,90,0) 75%),
      radial-gradient(ellipse 300px 90px at 180px 150px, rgba(122,74,34,0.85) 0%, rgba(122,74,34,0) 80%),
      radial-gradient(ellipse 260px 110px at 1150px 20px, rgba(138,163,182,0.9) 0%, rgba(138,163,182,0) 80%),
      linear-gradient(90deg, var(--sky-amber) 0%, var(--sky-gold) 35%, var(--sky-gold) 60%, var(--sky-amber) 80%, #9a8a78 100%);
  }
  .headline {
    position: absolute;
    left: 74px;
    top: 4px;
    width: 602px;
    text-align: center;
    font-weight: 900;
    font-size: 43px;
    line-height: 46px;
    color: var(--ink);
  }
  .subhead {
    position: absolute;
    left: 74px;
    top: 51px;
    width: 602px;
    text-align: center;
    font-weight: 700;
    font-size: 30px;
    line-height: 32px;
    color: var(--ink);
  }
  .offer {
    position: absolute;
    left: 74px;
    top: 102px;
    font-weight: 700;
    font-size: 23px;
    line-height: 28px;
    color: var(--ink);
    white-space: nowrap;
    letter-spacing: -0.2px;
  }
  .cta-button {
    position: absolute;
    left: 1023px;
    top: 16px;
    width: 150px;
    height: 62px;
    border-radius: 10px;
    border: 2px solid var(--btn-edge);
    background: linear-gradient(180deg, var(--btn-top), var(--btn-bottom));
    color: var(--white);
    font-family: "Lato", Arial, sans-serif;
    font-weight: 700;
    font-size: 21px;
    display: flex;
    align-items: center;
    justify-content: center;
    box-shadow: 0 2px 4px rgba(0,0,0,0.3);
  }
  .brand-name {
    position: absolute;
    left: 1010px;
    top: 96px;
    width: 176px;
    text-align: center;
    font-weight: 700;
    font-size: 30px;
    line-height: 40px;
    color: var(--white);
  }
</style>
</head>
<body>
  <div class="banner">
    <div class="sky-photo" role="img" aria-label="Sunlit golden sky with clouds and a person with arms raised in freedom on the right"></div>
    <h1 class="headline">Your Personal Privacy</h1>
    <p class="subhead">is threatened daily</p>
    <p class="offer">See what others can find out about you online with a free scan</p>
    <div class="cta-button">Get Started Now!</div>
    <div class="brand-name">QuillBranch</div>
  </div>
</body>
</html>
```